Heron Loan Partners Business Card

We need a business card design for our mortgage servicing company. In addition to servicing the loans of homeowners, we help homeowners with purchasing their homes and any mortgage refinancing. We would like to see designs that use the colors in the logo attached below (gold-ish yellow and navy blue), and any other design you deem fit! The design should communicate a simpler life with smart mortgages provided by Heron.

```html
<!DOCTYPE html>
<html lang="en">
<head>
<meta charset="utf-8">
<title>Heron Loan Partners Business Card</title>
<link href="https://fonts.googleapis.com/css2?family=Montserrat:wght@400;500;700;800&display=swap" rel="stylesheet">
<style>
  :root {
    --navy: #25205a;
    --gold: #e0b23c;
    --white: #ffffff;
    --ink: #1c1c24;
    --backdrop: #e9e9ec;
  }
  * { margin: 0; padding: 0; box-sizing: border-box; }
  html, body {
    width: 1200px; height: 880px; overflow: hidden;
    background: var(--backdrop);
    font-family: "Montserrat", Arial, sans-serif;
  }
  .card {
    position: absolute; left: 280px;
    width: 640px; height: 366px;
    overflow: hidden;
    box-shadow: 0 6px 18px rgba(0,0,0,0.18);
  }
  /* back side */
  .card-back { top: 36px; background: var(--navy); }
  .back-brand {
    position: absolute; inset: 0;
    display: flex; align-items: center; justify-content: center; gap: 16px;
  }
  .brand-dot { width: 22px; height: 22px; border-radius: 50%; background: var(--gold); }
  .back-brand .brand-name {
    color: var(--gold); font-weight: 800; font-size: 46px; letter-spacing: 0.5px;
  }
  /* front side */
  .card-front { top: 476px; background: var(--white); color: var(--ink); }
  .front-brand {
    position: absolute; top: 54px; right: 60px;
    display: flex; align-items: center; gap: 10px;
  }
  .front-brand .brand-dot { width: 14px; height: 14px; }
  .front-brand .brand-name { color: var(--navy); font-weight: 800; font-size: 26px; }
  .name-marker {
    position: absolute; left: 0; top: 150px; width: 26px; height: 34px; background: var(--gold);
  }
  .holder { position: absolute; left: 40px; top: 140px; }
  .holder-name { font-weight: 800; font-size: 18px; letter-spacing: 0.5px; color: var(--navy); }
  .holder-name .surname { color: var(--gold); }
  .holder-role { font-size: 15px; margin-top: 2px; }
  .contacts {
    position: absolute; left: 40px; top: 212px; list-style: none;
    font-size: 14px; line-height: 24px;
  }
  .contacts li { display: flex; align-items: center; gap: 10px; }
  .contacts svg { width: 14px; height: 14px; fill: var(--gold); }
  .address {
    position: absolute; right: 34px; top: 180px; text-align: right;
    font-size: 14px; line-height: 20px; font-weight: 500;
  }
  .bands { position: absolute; left: 0; bottom: 0; width: 640px; height: 130px; }
  .reg-number {
    position: absolute; right: 30px; bottom: 70px;
    color: var(--white); font-size: 14px; font-weight: 500;
  }
</style>
</head>
<body>
  <section class="card card-back" aria-label="Card back">
    <div class="back-brand">
      <span class="brand-dot"></span>
      <span class="brand-name">Heron Loan Partners</span>
    </div>
  </section>

  <section class="card card-front" aria-label="Card front">
    <div class="front-brand">
      <span class="brand-dot"></span>
      <span class="brand-name">Heron Loan Partners</span>
    </div>

    <div class="name-marker"></div>
    <div class="holder">
      <p class="holder-name">DALE <span class="surname">WHITCOMBE</span></p>
      <p class="holder-role">Owner</p>
    </div>

    <ul class="contacts">
      <li><svg viewBox="0 0 16 16"><path d="M3 1h3l1.5 4-2 1.5a9 9 0 0 0 4 4L11 8.5l4 1.5v3a2 2 0 0 1-2 2A12 12 0 0 1 1 3a2 2 0 0 1 2-2z"/></svg>555.014.2290</li>
      <li><svg viewBox="0 0 16 16"><path d="M1 3h14v10H1zM1.8 3.8 8 9l6.2-5.2z" fill-rule="evenodd"/></svg>info@heronloanpartners.com</li>
      <li><svg viewBox="0 0 16 16"><circle cx="8" cy="8" r="7"/></svg>www.heronloanpartners.com</li>
    </ul>

    <p class="address">2408 Alder Row, Ste<br>100, Fairview, TX 75069</p>

    <svg class="bands" viewBox="0 0 640 130" aria-hidden="true">
      <polygon points="0,68 418,68 416,76 0,76" fill="var(--gold)"/>
      <polygon points="0,84 414,84 408,130 0,130" fill="var(--navy)"/>
      <polygon points="436,130 446,20 640,20 640,130" fill="var(--gold)"/>
    </svg>
    <p class="reg-number">Reg Number: 480316</p>
  </section>
</body>
</html>
```